Classy, Elegant, Simple Business Card Design

Looking to have a classy, simple, and elegant design. Want a top notch designed business card. I really like the look of the new torvane credit card. I also like the design I attached. I am trying to reach 21-29 year old females for booking us for there wedding or event. We offer Disc Jockey Service, Photo Booth Rentals, and Uplighting .

Target Market(s)

21-28 year old females

Contact Information for Business Card

Has to have logo, website, email, and phone number

Font styles to use
Other font styles liked:
• open to font choice, modern, clean
Designer to choose
33a6d7
0791cd
0555a3
ffffff

Requirements
Must have
• Has to have logo, website, email, and phone number
Nice to have
• I really like the design of the new torvane credit card. I also included my logo and some designs I like
Should not have
• clutter or too much info

```html
<!DOCTYPE html>
<html lang="en">
<head>
<meta charset="utf-8">
<title>Larkfield Event Group – Business Card</title>
<link href="https://fonts.googleapis.com/css2?family=Josefin+Sans:wght@400&family=Work+Sans:wght@400;600&display=swap" rel="stylesheet">
<style>
  :root {
    --backdrop: #0e0e0e;
    --card: #1a1a1a;
    --card-edge: #262626;
    --silver: #cfcfcf;
    --silver-soft: #a9a9a9;
  }
  * { box-sizing: border-box; margin: 0; padding: 0; }
  html, body { width: 1200px; height: 900px; overflow: hidden; background: var(--backdrop); }
  .canvas {
    position: relative; width: 1200px; height: 900px;
    background: radial-gradient(circle at 60% 40%, #1c1c1c 0%, var(--backdrop) 70%);
  }
  .card {
    position: absolute; left: 285px; width: 630px; height: 360px;
    background: linear-gradient(135deg, var(--card) 0%, #202020 60%, var(--card) 100%);
    border: 1px solid var(--card-edge);
    box-shadow: 0 20px 40px rgba(0,0,0,.6);
  }
  .card-front { top: 60px; }
  .card-back { top: 480px; }

  .brand { display: flex; align-items: center; gap: 14px; color: var(--silver); font-family: "Josefin Sans", sans-serif; font-weight: 400; letter-spacing: 3px; }
  .brand-dot { width: 14px; height: 14px; border-radius: 50%; background: var(--silver); flex: none; }
  .brand-name { line-height: 1.15; text-transform: uppercase; }

  .card-front .brand { position: absolute; left: 50%; top: 50%; transform: translate(-50%, -50%); font-size: 30px; }

  .card-back .brand { position: absolute; left: 42px; top: 50%; transform: translateY(-50%); font-size: 24px; width: 250px; }
  .divider { position: absolute; left: 308px; top: 60px; width: 2px; height: 240px; background: var(--silver-soft); }

  .contact { position: absolute; left: 340px; top: 62px; font-family: "Work Sans", sans-serif; color: var(--silver); }
  .contact-name { font-size: 25px; font-weight: 600; letter-spacing: 1px; text-transform: uppercase; }
  .contact-role { font-size: 16px; color: var(--silver-soft); margin-top: 2px; }
  .contact-address { font-size: 16px; line-height: 1.4; margin-top: 18px; color: var(--silver-soft); }
  .contact-list { list-style: none; margin-top: 16px; font-size: 17px; }
  .contact-list li { display: flex; align-items: center; gap: 10px; line-height: 1.65; }
  .contact-list svg { width: 13px; height: 13px; flex: none; }
</style>
</head>
<body>
<main class="canvas">
  <section class="card card-front">
    <div class="brand"><span class="brand-dot"></span><span class="brand-name">Larkfield<br>Event Group</span></div>
  </section>

  <section class="card card-back">
    <div class="brand"><span class="brand-dot"></span><span class="brand-name">Larkfield<br>Event Group</span></div>
    <div class="divider"></div>
    <div class="contact">
      <p class="contact-name">Daniel Reyes</p>
      <p class="contact-role">Managing Partner</p>
      <p class="contact-address">418 W Harmon Ave.,<br>Pasadena, CA 91101</p>
      <ul class="contact-list">
        <li>
          <svg viewBox="0 0 16 16" fill="none" stroke="#cfcfcf" stroke-width="1.6" stroke-linecap="round"><path d="M4 1.5 6 5 4.5 6.5c1 2 3 4 5 5L11 10l3.5 2L13 14.5C7 14.5 1.5 9 1.5 3z"/></svg>
          555-214-0937
        </li>
        <li>
          <svg viewBox="0 0 16 16" fill="none" stroke="#cfcfcf" stroke-width="1.6"><rect x="1.5" y="3.5" width="13" height="9"/><path d="M1.5 3.5 8 9l6.5-5.5"/></svg>
          info@larkfieldevents.com
        </li>
        <li>
          <svg viewBox="0 0 16 16" fill="none" stroke="#cfcfcf" stroke-width="1.4"><circle cx="8" cy="8" r="6.5"/><ellipse cx="8" cy="8" rx="3" ry="6.5"/><path d="M1.5 8h13"/></svg>
          www.larkfieldevents.com
        </li>
      </ul>
    </div>
  </section>
</main>
</body>
</html>
```